Ledger Lanternfox Powerpoint with Marshal Valorline Type Theme

Need powerpoint template with matching colors and different slide options. Logo and colors to be used can be found at ledgerlanternfox.example. Want brightly colored slide deck that is readable form the back of a room, but highlights colors. I will be incorporating Quizzap into the slides to gamify my presentations.

Target Market(s)

Tech

Industry/Entity Type

IT, specifically database, but crossing over to mental health in IT, important note this is not for a company, this is just for a professional building a brand

Font styles to use
Sans Serif

Colors
0054AA
0677BA
7BADD7
CADEEF
E8F1F8
EB3D1F
EC4F4E
F09395
F8D3D4
FCEDEE

Requirements
Must have
• My Logo in the bottom corner, front page, a thank your page, question page, content page, content page with two columns, content page with graphs, and icons to be used in the primary colors of the logos, About Me Page, Break Slides, Demo break slide
Should not have
• Lighter shades of colors, I want to pop out where colors are used, I want spacing and font size to be readable from the back of a room, most likely black text and white background

```html
<!DOCTYPE html>
<html lang="en">
<head>
<meta charset="utf-8">
<title>Ledger Lanternfox – Presentation Template</title>
<link rel="stylesheet" href="https://fonts.googleapis.com/css2?family=Montserrat:wght@300;400;600;700;800&display=swap">
<style>
:root{
  --red:#e8332f;--red-deep:#c9201f;--navy:#0d3c80;--blue:#0054aa;--mid:#0677ba;--sky:#1ea3dc;
  --ink:#1f1f1f;--body:#555;--muted:#9a9a9a;--card:#e8e8e8;--white:#fff;
}
*{box-sizing:border-box}
html,body{margin:0;width:1143px;height:1200px;overflow:hidden;background:#fff;font-family:'Montserrat',sans-serif;color:var(--ink)}
.deck{position:absolute;left:26px;top:22px;display:grid;grid-template-columns:repeat(4,254px);grid-auto-rows:143px;column-gap:25px;row-gap:26px}
.slide{position:relative;overflow:hidden;background:#fff;box-shadow:0 2px 7px rgba(0,0,0,.25)}
.abs{position:absolute}
.photo{position:absolute;inset:0}
.brand{position:absolute;left:18px;bottom:4px;font-size:3.4px;font-weight:700;color:var(--blue);display:flex;align-items:center;gap:1.5px}
.brand::before{content:"";width:3.6px;height:3.6px;border-radius:50%;background:var(--red)}
.url{position:absolute;right:18px;bottom:4.5px;font-size:2.4px;color:#aaa;word-spacing:3px}
.h{font-weight:300;font-size:12px;line-height:1.12;margin:0}
.h b{font-weight:700}
.sub{font-size:2.6px;color:var(--muted);margin-top:2px}
.p{font-size:2.5px;line-height:1.55;color:var(--body);margin:0;text-align:justify}
.mark{font-weight:700;color:var(--red);text-align:center;line-height:1.05}
.bul{margin:0;padding-left:5px;font-size:2.5px;line-height:1.55;color:var(--body)}
.bul li{margin-bottom:1.5px}
.tick{flex:none;width:11px;height:11px;border-radius:50%;background:linear-gradient(#e6e6e6,#c9c9c9);position:relative;display:block}
.tick::after{content:"";position:absolute;left:3.8px;top:2.4px;width:2.6px;height:4.6px;border:solid #6d6d6d;border-width:0 .9px .9px 0;transform:rotate(45deg)}
.tick.r{background:radial-gradient(circle at 40% 35%,#f0504d,var(--red-deep))}
.tick.n{background:radial-gradient(circle at 40% 35%,#2c64b0,var(--navy))}
.tick.r::after,.tick.n::after{border-color:#fff}
.bi{position:absolute;display:flex;align-items:center;gap:4px;width:104px}
.bi b{display:block;font-size:3.1px;font-weight:700;margin-bottom:1px}
.bi span{display:block;font-size:2.4px;line-height:1.4;color:var(--body)}
.bi.light b,.bi.light span{color:#fff}
.card{position:absolute;background:var(--card);border-top:1.6px solid var(--navy);padding:4px;box-shadow:0 1px 3px rgba(0,0,0,.15)}
.card.red{border-color:var(--red)}.card.sky{border-color:var(--sky)}.card.grey{border-color:#999}
.card h4{margin:0 0 3px;font-size:2.7px;font-weight:700;line-height:1.2}
.card ol{margin:0;padding-left:4px;font-size:2.05px;line-height:1.45;color:var(--body)}
.card ol li{margin-bottom:1.5px}
.num{font-weight:600;font-size:11px;line-height:1}
.stat{position:absolute;left:120px;width:116px;height:19px;padding:3px 7px;color:#fff}
.stat b{display:block;font-size:4.2px}
.stat span{display:block;font-size:2.2px;line-height:1.35}
.band{position:absolute;left:104px;width:138px;height:26px;display:flex;align-items:center;gap:8px;padding-left:8px;color:#fff}
.band b{display:block;font-size:2.8px;font-weight:400}
.band span{display:block;font-size:2.2px;line-height:1.4}
.ag-row{display:flex;gap:5px;align-items:flex-start;height:12.6px}
.ag-row .n{font-size:7.5px;color:var(--red);line-height:1;width:11px}
.ag-row b{display:block;font-size:3.6px;font-weight:400}
.ag-row span{display:block;font-size:2.3px;color:var(--muted)}
.contact{position:absolute;left:24px;display:flex;align-items:center;gap:3px;font-size:2.8px;color:#fff}
</style>
</head>
<body>
<main class="deck">

<!-- 1 Title -->
<section class="slide">
  <div class="photo" role="img" aria-label="Dark photo of a laptop keyboard with a superhero emblem" style="background:linear-gradient(120deg,#27344f,#111a2b 60%,#0b0f18)"></div>
  <div class="mark abs" style="left:20px;top:52px;width:90px;font-size:11px">Ledger Lanternfox</div>
  <div class="abs" style="left:122px;top:-26px;width:180px;height:196px;border-radius:50%;background:rgba(222,222,224,.93)"></div>
  <div class="abs" style="left:158px;top:40px;width:92px;font-size:10px;font-weight:300;line-height:1.2;color:#2a5fa2">Your title Presentation Title Template goes here</div>
  <div class="abs" style="left:160px;top:116px;width:80px;text-align:right;color:#2a5fa2"><div style="font-size:4.4px">Tess Marrowby</div><div style="font-size:2.3px">Data Platform Fellow, Community Spark 2020 Award winner</div></div>
</section>

<!-- 2 Title blue -->
<section class="slide">
  <div class="photo" role="img" aria-label="Blue background of code and data charts" style="background:linear-gradient(160deg,#1c8dca,#0c6eae 70%,#0a5f99)"></div>
  <div class="mark abs" style="left:0;right:0;top:34px;font-size:15px">Ledger Lanternfox</div>
  <div class="abs" style="left:0;right:0;top:90px;text-align:center;color:#fff;font-size:9.5px;font-weight:300;letter-spacing:.5px;line-height:1.3">Your title Presentation Title<br>Template goes here</div>
  <div class="abs" style="left:0;right:0;top:122px;text-align:center;color:#fff"><div style="font-size:4.4px">Tess Marrowby</div><div style="font-size:2.3px">Data Platform Fellow, Community Spark 2020 Award winner</div></div>
</section>

<!-- 3 Agenda -->
<section class="slide">
  <div class="abs" style="left:22px;top:44px"><p class="h">Agenda</p><div class="sub">Table Of Contents</div></div>
  <div class="abs" style="left:120px;top:34px">
    <div class="ag-row"><span class="n">01</span><div><b>Introduction</b><span>Lorem Ipsum is simply dummy text of the printing</span></div></div>
    <div class="ag-row"><span class="n">02</span><div><b>Topic #1</b><span>Lorem Ipsum is simply dummy text of the printing</span></div></div>
    <div class="ag-row"><span class="n">03</span><div><b>Topic #2</b><span>Lorem Ipsum is simply dummy text of the printing</span></div></div>
    <div class="ag-row"><span class="n">04</span><div><b>Topic #3</b><span>Lorem Ipsum is simply dummy text of the printing</span></div></div>
    <div class="ag-row"><span class="n">05</span><div><b>Topic #4</b><span>Lorem Ipsum is simply dummy text of the printing</span></div></div>
    <div class="ag-row"><span class="n">06</span><div><b>Topic #5</b><span>Lorem Ipsum is simply dummy text of the printing</span></div></div>
    <div class="ag-row"><span class="n">07</span><div><b>Appendix</b><span>Lorem Ipsum is simply dummy text of the printing</span></div></div>
  </div>
  <div class="brand">Ledger Lanternfox</div><div class="url">ledgerlanternfox.example 3</div>
</section>

<!-- 4 About me -->
<section class="slide">
  <div class="abs" role="img" aria-label="Portrait photo in front of fireworks" style="left:18px;top:28px;width:80px;height:86px;background:linear-gradient(135deg,#c4384a,#4a3a6e 55%,#1f2a4a)"></div>
  <div class="abs" style="left:106px;top:26px;width:136px">
    <p class="h">About <b>Me</b></p>
    <div style="font-size:4.6px;font-weight:300">Tess Marrowby</div>
    <div style="font-size:2.2px;color:var(--body);margin-bottom:3px">Data Platform Fellow, Community Spark 2020 Award winner</div>
    <p class="p" style="margin-bottom:2px">Works as a senior database administrator and has spent many years tuning servers, leading a local user group and mentoring new speakers across the data community.</p>
    <p class="p" style="margin-bottom:2px">Outside of work she volunteers as a child advocate and speaks openly about mental health in technology, helping teams build kinder, healthier habits.</p>
    <p class="p">You may reach me on social media.</p>
  </div>
  <div class="brand">Ledger Lanternfox</div><div class="url">ledgerlanternfox.example 4</div>
</section>

<!-- 5 Title slide A -->
<section class="slide">
  <div class="abs" style="left:20px;top:18px"><p class="h">Your title slide<br><b>will be here</b></p><div class="sub" style="padding-left:8px">Your great Subtitle goes Here</div></div>
  <div class="abs" style="left:111px;top:20px;width:.5px;height:30px;background:#bbb"></div>
  <p class="p abs" style="left:116px;top:20px;width:124px">Lorem Ipsum is simply dummy text of the printing and typesetting industry. Lorem Ipsum has been the industry's standard dummy text ever since the 1500s, when an unknown printer took a galley of type and scrambled it to make a type specimen book.</p>
  <ul class="bul abs" style="left:116px;top:60px;width:124px">
    <li>Lorem Ipsum is simply dummy text of the printing and typesetting industry, standard dummy text ever since the 1500s.</li>
    <li>It has survived not only five centuries, but also the leap into electronic typesetting, remaining essentially unchanged.</li>
    <li>It was popularised in the 1960s with the release of sheets containing Lorem Ipsum passages.</li>
    <li>Lorem Ipsum has been the industry's standard dummy text ever since the 1500s.</li>
  </ul>
  <div class="mark abs" style="left:22px;top:70px;width:80px;font-size:11px">Ledger Lanternfox</div>
  <div class="brand">Ledger Lanternfox</div><div class="url">ledgerlanternfox.example 5</div>
</section>

<!-- 6 Title slide B -->
<section class="slide">
  <div class="abs" style="left:20px;top:18px"><p class="h" style="font-size:13px">Your title slide<br><b>will be here</b></p></div>
  <div class="abs" style="left:130px;top:20px;width:.5px;height:28px;background:#bbb"></div>
  <p class="p abs" style="left:136px;top:20px;width:104px">Lorem Ipsum is simply dummy text of the printing and typesetting industry. Lorem Ipsum has been the industry's standard dummy text ever since the 1500s, when an unknown printer took a galley of type.</p>
  <ul class="bul abs" style="left:20px;top:58px;width:112px">
    <li>Lorem Ipsum is simply dummy text of the printing and typesetting industry, standard dummy text ever since the 1500s.</li>
    <li>It has survived not only five centuries, but also the leap into electronic typesetting, remaining essentially unchanged.</li>
    <li>It was popularised in the 1960s with the release of sheets containing Lorem Ipsum passages.</li>
    <li>Lorem Ipsum has been the industry's standard dummy text ever since the 1500s.</li>
  </ul>
  <div class="mark abs" style="left:146px;top:66px;width:90px;font-size:12px">Ledger Lanternfox</div>
  <div class="brand">Ledger Lanternfox</div><div class="url">ledgerlanternfox.example 6</div>
</section>

<!-- 7 Demo blue -->
<section class="slide">
  <div class="photo" role="img" aria-label="Light blue background of source code" style="background:linear-gradient(150deg,#3db2e4,#1f9bd6 60%,#1489c7)"></div>
  <div class="abs" style="left:60px;top:14px;width:140px;font-size:10px;font-weight:700;color:var(--navy);text-align:center">Ledger Lanternfox</div>
  <div class="abs" style="left:32px;top:52px;color:#fff;font-size:19px;font-weight:300;line-height:1.1">Demo<br>slide<br>title</div>
  <div class="bi light" style="left:136px;top:54px"><i class="tick n"></i><div><b>Lorem Ipsum is simply dummy text</b><span>Lorem Ipsum is simply dummy text of the printing and typesetting industry.</span></div></div>
  <div class="bi light" style="left:136px;top:78px"><i class="tick r"></i><div><b>Lorem Ipsum is simply dummy text</b><span>Lorem Ipsum is simply dummy text of the printing and typesetting industry.</span></div></div>
  <div class="bi light" style="left:136px;top:102px"><i class="tick"></i><div><b>Lorem Ipsum is simply dummy text</b><span>Lorem Ipsum is simply dummy text of the printing and typesetting industry.</span></div></div>
  <div class="brand" style="color:#fff">Ledger Lanternfox</div>
</section>

<!-- 8 Demo grey -->
<section class="slide">
  <div class="photo" role="img" aria-label="Pale grey background of source code" style="background:linear-gradient(150deg,#e9e9ea,#d4d5d7)"></div>
  <p class="h abs" style="left:17px;top:16px;font-size:14px;color:#2a5fa2">Demo slide title</p>
  <div class="mark abs" style="left:18px;top:60px;width:100px;font-size:12px">Ledger Lanternfox</div>
  <div class="bi" style="left:136px;top:46px"><i class="tick n"></i><div><b>Lorem Ipsum is simply dummy text</b><span>Lorem Ipsum is simply dummy text of the printing and typesetting industry.</span></div></div>
  <div class="bi" style="left:136px;top:72px"><i class="tick r"></i><div><b>Lorem Ipsum is simply dummy text</b><span>Lorem Ipsum is simply dummy text of the printing and typesetting industry.</span></div></div>
  <div class="bi" style="left:136px;top:98px"><i class="tick"></i><div><b>Lorem Ipsum is simply dummy text</b><span>Lorem Ipsum is simply dummy text of the printing and typesetting industry.</span></div></div>
  <div class="brand">Ledger Lanternfox</div><div class="url">ledgerlanternfox.example 8</div>
</section>

<!-- 9 Red blank -->
<section class="slide" style="background:var(--red)">
  <div class="abs" style="left:14px;top:11px;font-size:5.5px;font-weight:700;color:#fff">Ledger Lanternfox</div>
</section>

<!-- 10 Navy blank -->
<section class="slide" style="background:var(--navy)">
  <div class="abs" style="left:14px;top:11px;font-size:5.5px;font-weight:700;color:#fff">Ledger Lanternfox</div>
</section>

<!-- 11 Break section -->
<section class="slide">
  <div class="photo" role="img" aria-label="Photo of a laptop keyboard and code on screen" style="background:linear-gradient(135deg,#2a3140,#12161f 70%)"></div>
  <svg class="abs" style="inset:0" width="254" height="143" viewBox="0 0 254 143"><path d="M150 0H254V143H122C108 100 112 40 150 0Z" fill="#e8332f"/></svg>
  <div class="abs" style="left:150px;top:26px;width:90px;text-align:center;font-size:8px;font-weight:700;color:#fff">Ledger Lanternfox</div>
  <div class="abs" style="left:140px;top:72px;width:110px;text-align:center;color:#fff"><div style="font-size:14px;font-weight:300;line-height:1.15;letter-spacing:.5px">BREAKE<br>SECTION</div><div style="font-size:4.4px;letter-spacing:1px;margin-top:1px">BULLETS SLIDES</div></div>
  <div class="url" style="color:#fbd">ledgerlanternfox.example 12</div>
</section>

<!-- 12 Stats -->
<section class="slide">
  <div class="abs" style="left:18px;top:14px"><p class="h" style="font-size:11.5px">Your title<br><b>slide here</b></p><div class="sub">Great Subtitle Here</div></div>
  <div class="abs" style="left:81px;top:16px;width:.5px;height:30px;background:#bbb"></div>
  <p class="p abs" style="left:86px;top:16px;width:154px">Lorem Ipsum is simply dummy text of the printing and typesetting industry. Lorem Ipsum has been the industry's standard dummy text ever since the 1500s, when an unknown printer took a galley of type and scrambled it to make a type specimen book. It has survived not only five centuries, but also the leap into electronic typesetting.</p>
  <p class="p abs" style="left:18px;top:56px;width:96px">Lorem Ipsum is simply dummy text of the printing and typesetting industry. Lorem Ipsum has been the industry's standard dummy text ever since the 1500s, when an unknown printer took a galley of type and scrambled it to make a type specimen book. It has survived not only five centuries, but also the leap into electronic typesetting, remaining essentially unchanged. It was popularised in the 1960s with the release.</p>
  <div class="stat" style="top:54px;background:var(--navy)"><b>1500+</b><span>Lorem Ipsum is simply dummy text of the printing and typesetting industry.</span></div>
  <div class="stat" style="top:78px;background:var(--red)"><b>900+</b><span>Lorem Ipsum is simply dummy text of the printing and typesetting industry.</span></div>
  <div class="stat" style="top:102px;background:var(--sky)"><b>2900+</b><span>Lorem Ipsum is simply dummy text of the printing and typesetting industry.</span></div>
  <div class="brand">Ledger Lanternfox</div><div class="url">ledgerlanternfox.example 7</div>
</section>

<!-- 13 Three elements -->
<section class="slide">
  <p class="h abs" style="left:0;right:0;top:22px;text-align:center">Three <b>elements slide</b></p>
  <div class="abs" style="left:20px;top:42px;width:64px;height:22px;background:var(--red);color:#fff;font-size:2.8px;padding:9px 6px">Element One</div>
  <div class="abs" style="left:20px;top:72px;width:64px;height:22px;background:var(--navy);color:#fff;font-size:2.8px;padding:9px 6px">Element Two</div>
  <div class="abs" style="left:20px;top:102px;width:64px;height:22px;background:var(--sky);color:#fff;font-size:2.8px;padding:9px 6px">Element Three</div>
  <p class="p abs" style="left:88px;top:42px;width:146px;height:22px;padding:3px 4px;background:#f3f3f3">Lorem ipsum dolor sit amet, consectetur adipiscing elit. Curabitur egestas gravida porttitor. Nullam egestas mi eget lacus aliquam viverra. In hac habitasse platea dictumst.</p>
  <p class="p abs" style="left:88px;top:72px;width:146px;height:22px;padding:3px 4px;background:#f3f3f3">Lorem ipsum dolor sit amet, consectetur adipiscing elit. Curabitur egestas gravida porttitor. Nullam egestas mi eget lacus aliquam viverra. In hac habitasse platea dictumst.</p>
  <p class="p abs" style="left:88px;top:102px;width:146px;height:22px;padding:3px 4px;background:#f3f3f3">Lorem ipsum dolor sit amet, consectetur adipiscing elit. Curabitur egestas gravida porttitor. Nullam egestas mi eget lacus aliquam viverra. In hac habitasse platea dictumst.</p>
  <div class="brand">Ledger Lanternfox</div><div class="url">ledgerlanternfox.example 13</div>
</section>

<!-- 14 Text and bullets A -->
<section class="slide">
  <div class="abs" style="left:20px;top:22px"><p class="h">Text and<br><b>Bullets Point</b><br>slide</p></div>
  <p class="p abs" style="left:20px;top:66px;width:80px">Lorem ipsum dolor sit amet, consectetur adipiscing elit. Curabitur egestas gravida porttitor. Nullam egestas mi eget lacus aliquam viverra. In hac habitasse platea dictumst. Nunc volutpat faucibus nisl, a dapibus mi feugiat in. Aenean posuere, urna sit amet accumsan ullamcorper.</p>
  <div class="bi" style="left:126px;top:24px"><i class="tick"></i><div><b>Lorem Ipsum is simply dummy text</b><span>Lorem Ipsum is simply dummy text of the printing and typesetting industry.</span></div></div>
  <div class="bi" style="left:126px;top:50px"><i class="tick r"></i><div><b>Lorem Ipsum is simply dummy text</b><span>Lorem Ipsum is simply dummy text of the printing and typesetting industry.</span></div></div>
  <div class="bi" style="left:126px;top:76px"><i class="tick"></i><div><b>Lorem Ipsum is simply dummy text</b><span>Lorem Ipsum is simply dummy text of the printing and typesetting industry.</span></div></div>
  <div class="bi" style="left:126px;top:102px"><i class="tick"></i><div><b>Lorem Ipsum is simply dummy text</b><span>Lorem Ipsum is simply dummy text of the printing and typesetting industry.</span></div></div>
  <div class="brand">Ledger Lanternfox</div><div class="url">ledgerlanternfox.example 14</div>
</section>

<!-- 15 Text and bullets B -->
<section class="slide">
  <div class="bi" style="left:20px;top:24px"><i class="tick"></i><div><b>Lorem Ipsum is simply dummy text</b><span>Lorem Ipsum is simply dummy text of the printing and typesetting industry.</span></div></div>
  <div class="bi" style="left:20px;top:50px"><i class="tick n"></i><div><b>Lorem Ipsum is simply dummy text</b><span>Lorem Ipsum is simply dummy text of the printing and typesetting industry.</span></div></div>
  <div class="bi" style="left:20px;top:76px"><i class="tick"></i><div><b>Lorem Ipsum is simply dummy text</b><span>Lorem Ipsum is simply dummy text of the printing and typesetting industry.</span></div></div>
  <div class="bi" style="left:20px;top:102px"><i class="tick"></i><div><b>Lorem Ipsum is simply dummy text</b><span>Lorem Ipsum is simply dummy text of the printing and typesetting industry.</span></div></div>
  <div class="abs" style="left:144px;top:22px"><p class="h">Text and<br><b>Bullets Point</b><br>slide</p></div>
  <p class="p abs" style="left:144px;top:66px;width:80px">Lorem ipsum dolor sit amet, consectetur adipiscing elit. Curabitur egestas gravida porttitor. Nullam egestas mi eget lacus aliquam viverra. In hac habitasse platea dictumst. Nunc volutpat faucibus nisl, a dapibus mi feugiat in. Aenean posuere, urna sit amet accumsan ullamcorper.</p>
  <div class="brand">Ledger Lanternfox</div><div class="url">ledgerlanternfox.example 15</div>
</section>

<!-- 16 Bullets point -->
<section class="slide">
  <p class="h abs" style="left:0;right:0;top:22px;text-align:center">Bullets <b>Point</b> slide</p>
  <div class="bi" style="left:20px;top:44px"><i class="tick r"></i><div><b>Lorem Ipsum is simply dummy text</b><span>Lorem Ipsum is simply dummy text of the printing and typesetting industry.</span></div></div>
  <div class="bi" style="left:20px;top:70px"><i class="tick"></i><div><b>Lorem Ipsum is simply dummy text</b><span>Lorem Ipsum is simply dummy text of the printing and typesetting industry.</span></div></div>
  <div class="bi" style="left:20px;top:96px"><i class="tick"></i><div><b>Lorem Ipsum is simply dummy text</b><span>Lorem Ipsum is simply dummy text of the printing and typesetting industry.</span></div></div>
  <div class="bi" style="left:136px;top:44px"><i class="tick n"></i><div><b>Lorem Ipsum is simply dummy text</b><span>Lorem Ipsum is simply dummy text of the printing and typesetting industry.</span></div></div>
  <div class="bi" style="left:136px;top:70px"><i class="tick"></i><div><b>Lorem Ipsum is simply dummy text</b><span>Lorem Ipsum is simply dummy text of the printing and typesetting industry.</span></div></div>
  <div class="bi" style="left:136px;top:96px"><i class="tick"></i><div><b>Lorem Ipsum is simply dummy text</b><span>Lorem Ipsum is simply dummy text of the printing and typesetting industry.</span></div></div>
  <div class="brand">Ledger Lanternfox</div><div class="url">ledgerlanternfox.example 16</div>
</section>

<!-- 17 Column break -->
<section class="slide">
  <div class="photo" role="img" aria-label="Dark photo of code on a monitor" style="background:linear-gradient(135deg,#1b2436,#0a0f18)"></div>
  <svg class="abs" style="inset:0" width="254" height="143" viewBox="0 0 254 143"><path d="M0 0H112C140 40 150 100 122 143H0Z" fill="#0d3c80"/></svg>
  <div class="abs" style="left:26px;top:32px;width:70px;text-align:center;font-size:7px;font-weight:700;color:#fff">Ledger Lanternfox</div>
  <div class="abs" style="left:30px;top:68px;color:#fff;font-size:12px;font-weight:300;line-height:1.3;letter-spacing:.6px">COLUMN<br>TEXT<br>SLIDES</div>
  <div class="url" style="color:#ccd">ledgerlanternfox.example 17</div>
</section>

<!-- 18 Two column -->
<section class="slide">
  <p class="h abs" style="left:0;right:0;top:22px;text-align:center">Two column <b>Text Slide</b></p>
  <div class="card red" style="left:17px;top:42px;width:100px;height:80px"><div class="num" style="color:var(--red);margin-bottom:5px">01</div><h4>Bullet points title slide here</h4><ul class="bul" style="font-size:2.1px"><li>Lorem Ipsum is simply dummy text of the printing and typesetting industry ever since the 1500s.</li><li>When an unknown printer took a galley of type and scrambled it to make a type specimen book.</li><li>Typesetting, remaining essentially unchanged. It was popularised in the 1960s.</li></ul></div>
  <div class="card" style="left:131px;top:42px;width:100px;height:80px"><div class="num" style="color:var(--navy);margin-bottom:5px">02</div><h4>Bullet points title slide here</h4><ul class="bul" style="font-size:2.1px"><li>Lorem Ipsum is simply dummy text of the printing and typesetting industry ever since the 1500s.</li><li>When an unknown printer took a galley of type and scrambled it to make a type specimen book.</li><li>Typesetting, remaining essentially unchanged. It was popularised in the 1960s.</li></ul></div>
  <div class="brand">Ledger Lanternfox</div><div class="url">ledgerlanternfox.example 18</div>
</section>

<!-- 19 Three column -->
<section class="slide">
  <p class="h abs" style="left:19px;top:22px">Three column <b>Text Slide</b></p>
  <div class="card" style="left:18px;top:42px;width:66px;height:82px"><h4>Bullet points &amp;<br>Title here</h4><ol><li>Lorem Ipsum is simply dummy text of the printing and typesetting industry since the 1500s.</li><li>When an unknown printer took a galley of type and scrambled it to make a type specimen book.</li><li>Typesetting, remaining essentially unchanged.</li></ol></div>
  <div class="card red" style="left:93px;top:42px;width:66px;height:82px"><h4>Bullet points &amp;<br>Title here</h4><ol><li>When an unknown printer took a galley of type and scrambled it to make a type specimen book.</li><li>Typesetting, remaining essentially unchanged. It was popularised in the 1960s.</li><li>Lorem Ipsum has been the industry's standard text.</li></ol></div>
  <div class="card sky" style="left:168px;top:42px;width:66px;height:82px"><h4>Bullet points &amp;<br>Title here</h4><ol><li>Nulla mollis arcu ut turpis bibendum, sed sagittis justo tincidunt.</li><li>Etiam vitae lorem eros. Nullam quis sem nunc. In laoreet arcu et erat mattis.</li><li>Suspendisse scelerisque massa erat, non efficitur orci.</li></ol></div>
  <div class="brand">Ledger Lanternfox</div><div class="url">ledgerlanternfox.example 19</div>
</section>

<!-- 20 Four column -->
<section class="slide">
  <p class="h abs" style="left:19px;top:22px">Four column <b>Text Slide</b></p>
  <div class="card" style="left:22px;top:42px;width:48px;height:82px"><h4>Bullet points &amp;<br>Title here</h4><ol><li>Lorem Ipsum is simply dummy text of the printing industry.</li><li>When an unknown printer took a galley of type.</li><li>Typesetting, remaining essentially unchanged.</li></ol></div>
  <div class="card red" style="left:76px;top:42px;width:48px;height:82px"><h4>Bullet points &amp;<br>Title here</h4><ol><li>When an unknown printer took a galley of type and scrambled it.</li><li>Typesetting, remaining essentially unchanged.</li><li>Lorem Ipsum has been the standard text.</li></ol></div>
  <div class="card grey" style="left:130px;top:42px;width:48px;height:82px"><h4>Bullet points &amp;<br>Title here</h4><ol><li>Nulla mollis arcu ut turpis bibendum, sed sagittis justo.</li><li>Etiam vitae lorem eros. Nullam quis sem nunc.</li><li>Suspendisse scelerisque massa erat.</li></ol></div>
  <div class="card grey" style="left:184px;top:42px;width:48px;height:82px"><h4>Bullet points &amp;<br>Title here</h4><ol><li>Nulla mollis arcu ut turpis bibendum, sed sagittis justo.</li><li>Etiam vitae lorem eros. Nullam quis sem nunc.</li><li>Suspendisse scelerisque massa erat.</li></ol></div>
  <div class="brand">Ledger Lanternfox</div><div class="url">ledgerlanternfox.example 20</div>
</section>

<!-- 21 Five column -->
<section class="slide">
  <p class="h abs" style="left:19px;top:22px">Five column <b>Text Slide</b></p>
  <div class="card" style="left:20px;top:44px;width:39px;height:78px"><h4>Bullet points &amp;<br>Title here</h4><ol><li>Lorem Ipsum is simply dummy text of the printing.</li><li>When an unknown printer took a galley.</li><li>Typesetting, remaining unchanged.</li></ol></div>
  <div class="card red" style="left:64px;top:44px;width:39px;height:78px"><h4>Bullet points &amp;<br>Title here</h4><ol><li>When an unknown printer took a galley of type.</li><li>Typesetting, remaining essentially unchanged.</li><li>Lorem Ipsum standard text.</li></ol></div>
  <div class="card grey" style="left:108px;top:44px;width:39px;height:78px"><h4>Bullet points &amp;<br>Title here</h4><ol><li>Nulla mollis arcu ut turpis bibendum.</li><li>Etiam vitae lorem eros, quis sem nunc.</li><li>Suspendisse massa erat.</li></ol></div>
  <div class="card grey" style="left:152px;top:44px;width:39px;height:78px"><h4>Bullet points &amp;<br>Title here</h4><ol><li>Nulla mollis arcu ut turpis bibendum.</li><li>Etiam vitae lorem eros, quis sem nunc.</li><li>Suspendisse massa erat.</li></ol></div>
  <div class="card grey" style="left:196px;top:44px;width:39px;height:78px"><h4>Bullet points &amp;<br>Title here</h4><ol><li>Nulla mollis arcu ut turpis bibendum.</li><li>Etiam vitae lorem eros, quis sem nunc.</li><li>Suspendisse massa erat.</li></ol></div>
  <div class="brand">Ledger Lanternfox</div><div class="url">ledgerlanternfox.example 21</div>
</section>

<!-- 22 Six column -->
<section class="slide">
  <p class="h abs" style="left:19px;top:18px">Six column <b>Text Slide</b></p>
  <div class="card grey" style="left:18px;top:37px;width:62px;height:42px"><h4>Bullet points &amp; Title here</h4><ol><li>Lorem Ipsum is simply dummy text of the printing industry.</li><li>When an unknown printer took a galley of type.</li><li>Typesetting, remaining essentially unchanged.</li></ol></div>
  <div class="card red" style="left:93px;top:37px;width:62px;height:42px"><h4>Bullet points &amp; Title here</h4><ol><li>When an unknown printer took a galley of type.</li><li>Typesetting, remaining essentially unchanged.</li><li>Lorem Ipsum has been the standard text.</li></ol></div>
  <div class="card grey" style="left:168px;top:37px;width:62px;height:42px"><h4>Bullet points &amp; Title here</h4><ol><li>Nulla mollis arcu ut turpis bibendum, sed sagittis.</li><li>Etiam vitae lorem eros. Nullam quis sem nunc.</li><li>Suspendisse scelerisque massa erat.</li></ol></div>
  <div class="card grey" style="left:18px;top:83px;width:62px;height:42px"><h4>Bullet points &amp; Title here</h4><ol><li>Lorem Ipsum is simply dummy text of the printing industry.</li><li>When an unknown printer took a galley of type.</li><li>Typesetting, remaining essentially unchanged.</li></ol></div>
  <div class="card" style="left:93px;top:83px;width:62px;height:42px"><h4>Bullet points &amp; Title here</h4><ol><li>When an unknown printer took a galley of type.</li><li>Typesetting, remaining essentially unchanged.</li><li>Lorem Ipsum has been the standard text.</li></ol></div>
  <div class="card sky" style="left:168px;top:83px;width:62px;height:42px"><h4>Bullet points &amp; Title here</h4><ol><li>Nulla mollis arcu ut turpis bibendum, sed sagittis.</li><li>Etiam vitae lorem eros. Nullam quis sem nunc.</li><li>Suspendisse scelerisque massa erat.</li></ol></div>
  <div class="brand">Ledger Lanternfox</div><div class="url">ledgerlanternfox.example 22</div>
</section>

<!-- 23 Three text point -->
<section class="slide">
  <div class="card" style="left:18px;top:16px;width:110px;height:34px;padding:3px"><h4 style="font-size:2.6px">Lorem Ipsum is simply dummy text</h4><p class="p" style="font-size:2.1px">Lorem Ipsum is simply dummy text of the printing and typesetting industry. Lorem Ipsum has been the industry's standard dummy text ever since the 1500s, when an unknown printer took a galley of type and scrambled it to make a type specimen book.</p></div>
  <div class="card red" style="left:18px;top:53px;width:110px;height:34px;padding:3px"><h4 style="font-size:2.6px">Lorem Ipsum is simply dummy text</h4><p class="p" style="font-size:2.1px">Lorem Ipsum is simply dummy text of the printing and typesetting industry. Lorem Ipsum has been the industry's standard dummy text ever since the 1500s, when an unknown printer took a galley of type and scrambled it to make a type specimen book.</p></div>
  <div class="card" style="left:18px;top:90px;width:110px;height:34px;padding:3px"><h4 style="font-size:2.6px">Lorem Ipsum is simply dummy text</h4><p class="p" style="font-size:2.1px">Lorem Ipsum is simply dummy text of the printing and typesetting industry. Lorem Ipsum has been the industry's standard dummy text ever since the 1500s, when an unknown printer took a galley of type and scrambled it to make a type specimen book.</p></div>
  <p class="h abs" style="left:124px;top:26px">Three Text<br><b>Point slide</b></p>
  <p class="p abs" style="left:124px;top:66px;width:112px">Lorem Ipsum is simply dummy text of the printing and typesetting industry. Lorem Ipsum has been the industry's standard dummy text ever since the 1500s, when an unknown printer took a galley of type and scrambled it to make a type specimen book. It has survived not only five centuries, but also the leap into electronic typesetting, remaining essentially unchanged.</p>
  <div class="brand">Ledger Lanternfox</div><div class="url">ledgerlanternfox.example 23</div>
</section>

<!-- 24 Icon bands -->
<section class="slide">
  <p class="h abs" style="left:18px;top:22px">Your title<br><b>slide will</b><br>be here</p>
  <p class="p abs" style="left:18px;top:76px;width:76px">Lorem Ipsum is simply dummy text of the printing and typesetting industry. Lorem Ipsum has been the industry's standard dummy text ever since the 1500s, when an unknown printer took a galley of type and scrambled it to make a type specimen book. It has survived not only five centuries.</p>
  <div class="band" style="top:24px;background:var(--navy)"><svg width="13" height="13" viewBox="0 0 24 24" fill="none" stroke="#fff" stroke-width="1.6"><rect x="3" y="3" width="8" height="6" rx="1"/><rect x="13" y="15" width="8" height="6" rx="1"/><path d="M7 9v4h10v2"/></svg><div><b>Subtitle Here</b><span>Lorem ipsum dolor sit amet, consectetur adipiscing elit. Nulla imperdiet volutpat dui at fermentum.</span></div></div>
  <div class="band" style="top:53px;background:var(--red)"><svg width="13" height="13" viewBox="0 0 24 24" fill="none" stroke="#fff" stroke-width="1.6"><path d="M7 18H6a4 4 0 0 1-.5-8A6 6 0 0 1 17 8.5 4.5 4.5 0 0 1 18 18h-1"/><path d="M12 11v9M9 17l3 3 3-3"/></svg><div><b>Subtitle Here</b><span>Lorem ipsum dolor sit amet, consectetur adipiscing elit. Nulla imperdiet volutpat dui at fermentum.</span></div></div>
  <div class="band" style="top:82px;background:var(--sky)"><svg width="13" height="13" viewBox="0 0 24 24" fill="none" stroke="#fff" stroke-width="1.6"><ellipse cx="12" cy="5" rx="7" ry="2.5"/><path d="M5 5v14c0 1.4 3.1 2.5 7 2.5s7-1.1 7-2.5V5M5 12c0 1.4 3.1 2.5 7 2.5s7-1.1 7-2.5"/></svg><div><b>Subtitle Here</b><span>Lorem ipsum dolor sit amet, consectetur adipiscing elit. Nulla imperdiet volutpat dui at fermentum.</span></div></div>
  <div class="brand">Ledger Lanternfox</div><div class="url">ledgerlanternfox.example 24</div>
</section>

<!-- 25 Numbered points -->
<section class="slide">
  <p class="h abs" style="left:0;right:0;top:20px;text-align:center">Your Title <b>Slide Here</b></p>
  <p class="p abs" style="left:20px;top:42px;width:94px">Lorem ipsum dolor sit amet, consectetur adipiscing elit. Curabitur egestas gravida porttitor. Nullam egestas mi eget lacus aliquam viverra. In hac habitasse platea dictumst. Nunc volutpat faucibus nisl, a dapibus mi feugiat in. Aenean posuere, urna sit amet accumsan ullamcorper, dolor orci gravida est, eget viverra turpis libero in nunc. Aenean aliquam metus in eros hendrerit elementum. Quisque venenatis, elit eget dapibus hendrerit, tortor neque aliquam nunc, sit amet mollis sapien ipsum a dui. Curabitur condimentum ante magna, sed tempor metus ullamcorper molestie.</p>
  <div class="abs" style="left:134px;top:42px;width:46px;text-align:center"><div class="num" style="color:var(--blue)">01</div><div style="font-size:2.4px;font-weight:600;margin:2px 0">Lorem ipsum dolor sit amet, consectetur</div><div class="p" style="text-align:center;font-size:2.1px">Frequently, your initial font choice is taken out of your awesome ha</div></div>
  <div class="abs" style="left:184px;top:42px;width:46px;text-align:center"><div class="num" style="color:var(--blue)">02</div><div style="font-size:2.4px;font-weight:600;margin:2px 0">Lorem ipsum dolor sit amet, consectetur</div><div class="p" style="text-align:center;font-size:2.1px">Frequently, your initial font choice is taken out of your awesome ha</div></div>
  <div class="abs" style="left:134px;top:88px;width:46px;text-align:center"><div class="num" style="color:var(--blue)">03</div><div style="font-size:2.4px;font-weight:600;margin:2px 0">Lorem ipsum dolor sit amet, consectetur</div><div class="p" style="text-align:center;font-size:2.1px">Frequently, your initial font choice is taken out of your awesome ha</div></div>
  <div class="abs" style="left:184px;top:88px;width:46px;text-align:center"><div class="num" style="color:var(--red)">04</div><div style="font-size:2.4px;font-weight:600;margin:2px 0">Lorem ipsum dolor sit amet, consectetur</div><div class="p" style="text-align:center;font-size:2.1px">Frequently, your initial font choice is taken out of your awesome ha</div></div>
  <div class="brand">Ledger Lanternfox</div><div class="url">ledgerlanternfox.example 25</div>
</section>

<!-- 26 Icon row -->
<section class="slide">
  <div class="abs" style="left:18px;top:20px"><p class="h">Your title<br><b>slide will</b><br>be here</p><div class="sub">Great Subtitle Here</div></div>
  <div class="abs" style="left:80px;top:20px;width:.5px;height:44px;background:#bbb"></div>
  <p class="p abs" style="left:84px;top:20px;width:154px">Lorem Ipsum is simply dummy text of the printing and typesetting industry. Lorem Ipsum has been the industry's standard dummy text ever since the 1500s, when an unknown printer took a galley of type and scrambled it to make a type specimen book. It has survived not only five centuries, but also the leap into electronic typesetting, remaining essentially unchanged. It was popularised in the 1960s with the release of sheets containing passages, and more recently with desktop publishing software.</p>
  <div class="abs" style="left:18px;top:84px;width:66px;display:flex;gap:4px"><svg width="12" height="8" viewBox="0 0 24 16" fill="none" stroke="#0d3c80" stroke-width="2"><path d="M1 8C5 2 19 2 23 8 19 14 5 14 1 8Z"/><circle cx="12" cy="8" r="3"/></svg><div><div style="font-size:2.8px;font-weight:600;color:var(--navy)">Lorem Ipsum is simply dummy text of the printing</div><p class="p" style="font-size:2.1px">1500s, when an unknown printer took a galley of type and scrambled it to make a type specimen book. It has survived not only five centuries, but also the leap into electronic typesetting.</p></div></div>
  <div class="abs" style="left:92px;top:84px;width:66px;display:flex;gap:4px"><svg width="10" height="12" viewBox="0 0 20 24" fill="none" stroke="#0d3c80" stroke-width="2"><path d="M10 2a7 7 0 0 0-4 12.7V18h8v-3.3A7 7 0 0 0 10 2Z"/><path d="M7 21h6"/></svg><div><div style="font-size:2.8px;font-weight:600;color:var(--navy)">Lorem Ipsum is simply dummy text of the printing</div><p class="p" style="font-size:2.1px">1500s, when an unknown printer took a galley of type and scrambled it to make a type specimen book. It has survived not only five centuries, but also the leap into electronic typesetting.</p></div></div>
  <div class="abs" style="left:166px;top:84px;width:66px;display:flex;gap:4px"><svg width="11" height="11" viewBox="0 0 24 24" fill="none" stroke="#0d3c80" stroke-width="2"><rect x="2" y="2" width="20" height="20" rx="2"/><path d="M7 7l4 4M11 7l-4 4M13 15h5M15.5 12.5v5"/></svg><div><div style="font-size:2.8px;font-weight:600;color:var(--navy)">Lorem Ipsum is simply dummy text of the printing</div><p class="p" style="font-size:2.1px">1500s, when an unknown printer took a galley of type and scrambled it to make a type specimen book. It has survived not only five centuries, but also the leap into electronic typesetting.</p></div></div>
  <div class="brand">Ledger Lanternfox</div><div class="url">ledgerlanternfox.example 26</div>
</section>

<!-- 27 Q&A -->
<section class="slide">
  <div class="photo" role="img" aria-label="Blue background of source code" style="background:linear-gradient(150deg,#1b54a4,#123e86 60%,#0d3170)"></div>
  <svg class="abs" style="inset:0" width="254" height="143" viewBox="0 0 254 143"><path d="M0 0H117L88 143H0Z" fill="#fff"/><path d="M0 112H200L196 117H0Z" fill="#e8332f"/></svg>
  <div class="abs" style="left:18px;top:22px;width:60px;text-align:center;font-size:6px;font-weight:700;color:var(--navy)">Ledger Lanternfox</div>
  <div class="abs" style="left:22px;top:62px;font-size:30px;font-weight:800;color:var(--navy);letter-spacing:-1px">Q&amp;A</div>
  <div class="url" style="color:#9bb">ledgerlanternfox.example 27</div>
</section>

<!-- 28 Thanks -->
<section class="slide">
  <div class="photo" role="img" aria-label="Red tinted city skyline photo" style="background:linear-gradient(120deg,#e33a36,#f05a55 55%,#e2403c)"></div>
  <svg class="abs" style="inset:0" width="254" height="143" viewBox="0 0 254 143"><path d="M0 25H108Q117 25 115 35L103 143H0Z" fill="#0d3c80"/></svg>
  <div class="abs" style="left:22px;top:34px;color:#fff;font-size:11px;font-weight:300;line-height:1.2">Contact<br>Information</div>
  <div class="contact" style="top:104px"><svg width="4" height="4" viewBox="0 0 10 10"><circle cx="5" cy="5" r="4.5" fill="#fff"/></svg>@youraccount</div>
  <div class="contact" style="top:112px"><svg width="4.5" height="4" viewBox="0 0 12 9" fill="none" stroke="#fff"><rect x=".5" y=".5" width="11" height="8"/><path d="M.5 .5 6 5l5.5-4.5"/></svg>your@account.com</div>
  <div class="contact" style="top:120px"><svg width="4.5" height="4" viewBox="0 0 12 10" fill="none" stroke="#fff"><rect x=".5" y=".5" width="11" height="7"/><path d="M3 9.5h6"/></svg>ledgerlanternfox.example</div>
  <div class="abs" style="left:134px;top:58px;width:110px;text-align:center;color:#fff"><div style="font-size:17px;font-weight:700;line-height:1">Thanks</div><div style="font-size:4px;margin-top:1px">For Your watching</div></div>
  <div class="url" style="color:#fcc">ledgerlanternfox.example 28</div>
</section>

</main>
</body>
</html>
```